20 year old business card needs re-design

We need to redesign our corporate business card look. We need something that appears more modern, eye catchy but professional.

Target Market(s)

manufacturing industry

Industry/Entity Type

Manufacturer

Contact Information for Business Card

One side can have the logo. Other side can have contact information.

Font styles to use
Serif

Colors
3277b5
33b8a4
ffffff

Requirements
Must have
• Eye catchy - need to standout from the crowd. company logo cannot change. Full name, job title, phone number and email address.
Should not have
• Fax, business address is not necessary.

```html
<!DOCTYPE html>
<html lang="en">
<head>
<meta charset="utf-8">
<title>Norvel Works – Business Card</title>
<link rel="stylesheet" href="https://fonts.googleapis.com/css2?family=Libre+Baskerville:wght@400;700&family=Roboto:wght@400;500&display=swap">
<style>
  :root {
    --stage: #2b2b2d;
    --card: #f1f1f1;
    --card-edge: #fafafa;
    --band: #0b4ea8;
    --panel-top: #2b3aa0;
    --panel-bottom: #1c2784;
    --teal: #33b8a4;
    --ink: #1b1b1b;
    --white: #ffffff;
  }
  * { box-sizing: border-box; margin: 0; padding: 0; }
  html, body { width: 1200px; height: 834px; overflow: hidden; }
  body {
    background: var(--stage);
    font-family: "Roboto", Arial, sans-serif;
    position: relative;
  }
  .card {
    position: absolute;
    left: 320px;
    width: 560px;
    height: 320px;
    background: linear-gradient(135deg, var(--card-edge), var(--card));
    overflow: hidden;
    box-shadow: 0 8px 24px rgba(0,0,0,.45);
  }
  .card--front { top: 52px; }
  .card--back { top: 462px; }

  .wordmark {
    display: flex;
    align-items: center;
    gap: 10px;
    font-family: "Libre Baskerville", Georgia, serif;
    font-weight: 700;
    color: var(--ink);
    letter-spacing: .5px;
    white-space: nowrap;
  }
  .wordmark__square {
    width: 16px; height: 16px;
    background: var(--band);
  }

  .card--front .wordmark {
    position: absolute;
    top: 102px; left: 0; right: 0;
    justify-content: center;
    font-size: 38px;
  }
  .tagline-band {
    position: absolute;
    left: 0; right: 0;
    top: 212px;
    height: 52px;
    background: var(--band);
    color: var(--white);
    display: flex;
    align-items: center;
    justify-content: center;
    text-align: center;
    font-size: 12.5px;
    line-height: 1.35;
  }

  .back-logo {
    position: absolute;
    left: 0; top: 0;
    width: 268px; height: 100%;
    display: flex;
    align-items: center;
    justify-content: center;
  }
  .back-logo .wordmark { font-size: 26px; }
  .back-logo .wordmark__square { width: 12px; height: 12px; }

  .contact-panel {
    position: absolute;
    left: 272px; top: 0;
    width: 288px; height: 100%;
    background: linear-gradient(160deg, var(--panel-top), var(--panel-bottom));
    border-left: 4px solid var(--teal);
    color: var(--white);
    padding: 86px 0 0 38px;
  }
  .contact-panel::before {
    content: "";
    position: absolute;
    left: -4px; top: 150px;
    border-top: 9px solid transparent;
    border-bottom: 9px solid transparent;
    border-left: 9px solid var(--teal);
  }
  .contact-name {
    font-family: "Libre Baskerville", Georgia, serif;
    font-weight: 700;
    font-size: 19px;
  }
  .contact-role {
    color: var(--teal);
    font-size: 13px;
    margin: 3px 0 18px;
  }
  .contact-list { list-style: none; }
  .contact-list li {
    display: flex;
    align-items: center;
    gap: 12px;
    font-size: 12.5px;
    margin-bottom: 11px;
  }
  .contact-list svg {
    width: 14px; height: 14px;
    stroke: var(--teal);
    fill: none;
    stroke-width: 1.6;
    flex: none;
  }
</style>
</head>
<body>

<section class="card card--front">
  <div class="wordmark"><span class="wordmark__square"></span>Norvel Works</div>
  <div class="tagline-band">International Manufacturing Solutions for OEM<br>customers in North America</div>
</section>

<section class="card card--back">
  <div class="back-logo">
    <div class="wordmark"><span class="wordmark__square"></span>Norvel Works</div>
  </div>
  <div class="contact-panel">
    <p class="contact-name">Daniel Reyes</p>
    <p class="contact-role">President</p>
    <ul class="contact-list">
      <li>
        <svg viewBox="0 0 16 16"><path d="M3 2h3l1.5 3.5-2 1.2a8 8 0 0 0 3.8 3.8l1.2-2L14 10v3a1 1 0 0 1-1 1A11 11 0 0 1 2 3a1 1 0 0 1 1-1z"/></svg>
        555-014-2200 x120
      </li>
      <li>
        <svg viewBox="0 0 16 16"><rect x="1.5" y="3.5" width="13" height="9"/><path d="M1.5 3.5 8 9l6.5-5.5"/></svg>
        dan@norvelworks.com
      </li>
      <li>
        <svg viewBox="0 0 16 16"><circle cx="8" cy="8" r="6.3"/><path d="M1.7 8h12.6M8 1.7c2.2 2 2.2 10.6 0 12.6M8 1.7c-2.2 2-2.2 10.6 0 12.6"/></svg>
        www.norvelworks.com
      </li>
    </ul>
  </div>
</section>

</body>
</html>
```